New Business card design to reflect rebrand

I would like a business card design with a good base colour for our new logo and also a placeholder for a profile pic of the card holder. the design needs to be editable to the point that we can easily change the picture of the person and use that design for printmerlo etc. we are looking at a metalic finish business card so will need a good base colour to bring out the finish.

Target Market(s)

prospective customers

Industry/Entity Type

Business

Contact Information for Business Card

I would like one editable design that we can change the name of the card holder and profile picture. The design need to be in a format that be send to printmerlo etc.

Our address is Fenwick Lodge, Copse Lane, Penmarrow, GU14 3TP Tel no. 01483 556172

Requirements
Must have
• place holder for a profile pic for the card holder. in AI or preferably PSD format

```html
<!DOCTYPE html>
<html lang="en">
<head>
<meta charset="utf-8">
<title>Corvane Workplace Services – Business Card</title>
<link href="https://fonts.googleapis.com/css2?family=Michroma&family=Montserrat:wght@400;500;600;700&display=swap" rel="stylesheet">
<style>
  :root {
    --page-bg: #2b2b2d;
    --card-black: #050505;
    --white: #ffffff;
    --silver: #d9dadc;
    --orange: #f26a2e;
    --slate: #4e6584;
    --photo-tone: #3a3030;
  }
  * { box-sizing: border-box; margin: 0; padding: 0; }
  html, body {
    width: 1200px; height: 900px; overflow: hidden;
    background: var(--page-bg);
    font-family: "Montserrat", Arial, sans-serif;
  }
  .sheet {
    width: 1200px; height: 900px;
    display: flex; flex-direction: column; align-items: center; justify-content: center;
    gap: 40px;
  }
  .card {
    position: relative;
    width: 700px; height: 400px;
    background: var(--card-black);
    box-shadow: 0 12px 30px rgba(0,0,0,.5);
    color: var(--white);
    overflow: hidden;
  }
  /* front */
  .card--front {
    display: flex; flex-direction: column; align-items: center; justify-content: center;
  }
  .front-brand {
    font-family: "Montserrat", sans-serif;
    font-weight: 700;
    font-size: 78px;
    letter-spacing: 6px;
    color: var(--silver);
    line-height: 1;
  }
  .front-tagline {
    margin-top: 14px;
    font-family: "Michroma", sans-serif;
    font-size: 22px;
    letter-spacing: 7px;
    color: var(--orange);
  }
  .front-web {
    margin-top: 12px;
    font-size: 19px;
    letter-spacing: 1px;
    color: var(--orange);
  }
  .front-web b { font-weight: 700; color: var(--white); }

  /* back */
  .back-brand {
    position: absolute; right: 50px; top: 50px;
    display: flex; align-items: center; gap: 14px;
    font-family: "Montserrat", sans-serif;
    font-weight: 700;
    font-size: 52px;
    letter-spacing: 4px;
    color: var(--slate);
  }
  .back-brand .brand-dot {
    width: 22px; height: 22px; border-radius: 50%;
    background: var(--orange);
  }
  .rule {
    position: absolute; left: 244px; top: 150px;
    width: 416px; height: 1.5px;
    background: var(--white);
  }
  .profile-frame {
    position: absolute; left: 44px; top: 100px;
    width: 200px; height: 200px;
    border: 1.5px solid var(--white);
    padding: 6px;
  }
  .profile-photo {
    width: 100%; height: 100%;
    background: radial-gradient(circle at 50% 40%, #6b5248 0%, var(--photo-tone) 55%, #0c0c0c 100%);
  }
  .holder {
    position: absolute; left: 390px; top: 176px;
  }
  .holder-name {
    font-family: "Michroma", sans-serif;
    font-size: 21px;
    letter-spacing: 1px;
    color: var(--orange);
  }
  .holder-title {
    margin-top: 4px;
    font-family: "Montserrat", sans-serif;
    font-weight: 700;
    font-size: 15px;
    letter-spacing: 0.5px;
    color: var(--white);
  }
  .holder-address {
    margin-top: 12px;
    padding-left: 4px;
    font-size: 14px; line-height: 1.45;
  }
  .contact-list { margin-top: 10px; list-style: none; font-size: 14px; }
  .contact-list li { display: flex; align-items: center; gap: 10px; line-height: 1.55; }
  .contact-list svg { width: 12px; height: 12px; flex: none; }
  .contact-list b { color: var(--orange); font-weight: 700; }
</style>
</head>
<body>
<main class="sheet">
  <section class="card card--front" aria-label="Card front">
    <div class="front-brand">CORVANE</div>
    <div class="front-tagline">WORKPLACE SERVICES</div>
    <div class="front-web">www.<b>corvane</b>.com</div>
  </section>

  <section class="card card--back" aria-label="Card back">
    <div class="back-brand"><span class="brand-dot"></span>CORVANE</div>
    <div class="rule"></div>
    <div class="profile-frame">
      <div class="profile-photo" role="img" aria-label="Profile photo of the card holder"></div>
    </div>
    <div class="holder">
      <div class="holder-name">MARTIN ELLERY</div>
      <div class="holder-title">DIRECTOR</div>
      <div class="holder-address">Fenwick Lodge, Copse Lane<br>Penmarrow, GU14 3TP</div>
      <ul class="contact-list">
        <li>
          <svg viewBox="0 0 24 24" aria-hidden="true"><path fill="#f26a2e" d="M6.6 10.8a15.1 15.1 0 0 0 6.6 6.6l2.2-2.2c.3-.3.7-.4 1-.2 1.1.4 2.3.6 3.6.6.6 0 1 .4 1 1V20c0 .6-.4 1-1 1A17 17 0 0 1 3 4c0-.6.4-1 1-1h3.5c.6 0 1 .4 1 1 0 1.3.2 2.5.6 3.6.1.3 0 .7-.2 1z"/></svg>
          01483 556172
        </li>
        <li>
          <svg viewBox="0 0 24 24" aria-hidden="true"><rect x="2" y="5" width="20" height="14" rx="2" fill="none" stroke="#f26a2e" stroke-width="2.4"/><path d="M3 6l9 7 9-7" fill="none" stroke="#f26a2e" stroke-width="2.4"/></svg>
          info@corvane.com
        </li>
        <li>
          <svg viewBox="0 0 24 24" aria-hidden="true"><circle cx="12" cy="12" r="10" fill="#f26a2e"/><path d="M2 12h20M12 2c3 3 3 17 0 20M12 2c-3 3-3 17 0 20" fill="none" stroke="#050505" stroke-width="1.6"/></svg>
          <span>www.<b>corvane</b>.com</span>
        </li>
      </ul>
    </div>
  </section>
</main>
</body>
</html>
```